Design a New Business Card for Our Company

We are looking for fresh, unique, and a modern business card that reflects our roots as digital marketing agency focused on SEM.

Industry/Entity Type

Marketing

Contact Information for Business Card

looking for very unique out of the box designs. clean and modern that compliments our logo

Requirements
Must have
• colors should match our logo
• Front should have name, address, email, and phone/fax of the person, phone/fax are the same number
• back should have our url

```html
<!DOCTYPE html>
<html lang="en">
<head>
<meta charset="utf-8">
<title>Brightpath Media – Business Card</title>
<link rel="stylesheet" href="https://fonts.googleapis.com/css2?family=Open+Sans:wght@400;700;800&display=swap">
<style>
  :root {
    --canvas: #bdbdbb;
    --brand-blue: #5b97d1;
    --brand-black: #000000;
    --brand-grey: #b3b3b3;
    --paper-white: #ffffff;
    --ink: #111111;
  }
  * { box-sizing: border-box; margin: 0; padding: 0; }
  html, body {
    width: 1200px; height: 900px; overflow: hidden;
    background: var(--canvas);
    font-family: "Open Sans", Arial, sans-serif;
  }
  .stage { position: relative; width: 1200px; height: 900px; }

  .card {
    position: absolute;
    width: 600px; height: 343px;
    overflow: hidden;
    box-shadow: 0 6px 18px rgba(0,0,0,.25);
  }

  /* Back side: company name and website */
  .card--back {
    left: 380px; top: 70px;
    background: var(--brand-blue);
  }
  .card--back .brand {
    position: absolute; left: 0; right: 0; top: 118px;
    display: flex; justify-content: center; align-items: center; gap: 16px;
  }
  .brand__dot {
    width: 40px; height: 40px; border-radius: 50%;
    background: var(--brand-black);
  }
  .brand__name {
    font-weight: 800; font-size: 40px; letter-spacing: -0.5px;
    color: var(--brand-black); line-height: 1;
  }
  .card--back .website {
    position: absolute; left: 0; right: 0; top: 232px;
    text-align: center;
    font-weight: 700; font-size: 15px; color: var(--ink);
  }

  /* Front side: person and contact details */
  .card--front {
    left: 220px; top: 480px;
    background: var(--brand-blue);
  }
  .card--front .shapes { position: absolute; inset: 0; }
  .card--front .front-brand {
    position: absolute; left: 50px; top: 150px;
    display: flex; align-items: center; gap: 12px;
  }
  .front-brand .brand__dot { width: 30px; height: 30px; background: var(--brand-grey); }
  .front-brand .brand__name { font-size: 28px; color: var(--brand-grey); }

  .contact {
    position: absolute; right: 28px; top: 32px;
    text-align: right; color: var(--paper-white);
  }
  .contact__name { font-weight: 700; font-size: 20px; line-height: 1.2; }
  .contact__title { font-size: 16px; line-height: 1.2; margin-bottom: 30px; }
  .contact__line {
    display: flex; justify-content: flex-end; align-items: center; gap: 10px;
    font-size: 16px; line-height: 1.35;
  }
  .contact__line svg { width: 13px; height: 13px; flex: none; fill: var(--paper-white); }
  .contact__group + .contact__group { margin-top: 18px; }
  .contact__address { font-size: 17px; line-height: 1.3; }
  .contact__address--plain { margin-right: 23px; }
</style>
</head>
<body>
<main class="stage">

  <section class="card card--back" aria-label="Business card back">
    <div class="brand">
      <span class="brand__dot"></span>
      <span class="brand__name">Brightpath Media</span>
    </div>
    <p class="website">www.bpmedia.com</p>
  </section>

  <section class="card card--front" aria-label="Business card front">
    <svg class="shapes" viewBox="0 0 600 343" width="600" height="343" aria-hidden="true">
      <path d="M0 0 H318 C450 70 420 270 262 343 H0 Z" fill="var(--brand-grey)"/>
      <path d="M0 0 H296 C430 70 396 270 232 343 H0 Z" fill="var(--brand-black)"/>
    </svg>

    <div class="front-brand">
      <span class="brand__dot"></span>
      <span class="brand__name">Brightpath</span>
    </div>

    <div class="contact">
      <p class="contact__name">Daniel Hayes</p>
      <p class="contact__title">Managing Director</p>

      <div class="contact__group">
        <p class="contact__line">555.210.4836
          <svg viewBox="0 0 16 16"><path d="M1 5c0-2 3-3 7-3s7 1 7 3v1h-4V4.5H5V6H1zM3 7h10l1 6H2z"/></svg>
        </p>
        <p class="contact__line">555.210.4836
          <svg viewBox="0 0 16 16"><path d="M3 1h7v4h3v10H3zM5 3v3h3V3zM5 8h2v2H5zm3 0h2v2H8zm-3 3h2v2H5zm3 0h2v2H8z"/></svg>
        </p>
        <p class="contact__line">dan@bpmedia.com
          <svg viewBox="0 0 16 16"><path d="M1 3h14v10H1zm1.5 1.5L8 9l5.5-4.5z"/></svg>
        </p>
      </div>

      <div class="contact__group">
        <p class="contact__line contact__address">48 Harbor Lane
          <svg viewBox="0 0 16 16"><path d="M8 1a5 5 0 0 1 5 5c0 4-5 9-5 9S3 10 3 6a5 5 0 0 1 5-5zm0 3a2 2 0 1 0 0 4 2 2 0 0 0 0-4z"/></svg>
        </p>
        <p class="contact__line contact__address contact__address--plain">Portland, OR 97201</p>
      </div>
    </div>
  </section>

</main>
</body>
</html>
```